Chimney Service company needs new business card design

We need a updated business card with our new logo added. We provide a full range of chimney services throughout Vermont and New Hampshire. The business card will be one sided and color. Attached is our current business card another document showing all the information we would like on the card.
We dont like a lot of flashy colors.... here is a link to our website to get an idea of our branding www.flueguardianvt.example

Target Market(s)

homeowners

Industry/Entity Type

Business

Contact Information for Business Card

See attached sheet for content.

Font styles to use
Serif
Sans Serif

Requirements
Must have
• all information provided on separate sheet
Should not have
• Additional information that may clogg up design

```html
<!DOCTYPE html>
<html lang="en">
<head>
<meta charset="utf-8">
<title>Flue Guardian — Business Card</title>
<link href="https://fonts.googleapis.com/css2?family=Open+Sans:wght@400;600&family=Roboto:wght@400;700;900&display=swap" rel="stylesheet">
<style>
  :root {
    --brand-red: #8e0a0c;
    --charcoal: #333333;
    --ink: #2b2b2b;
    --card-white: #f3f3f3;
    --stage: #c4c4c4;
    --sliver: #3a3a3a;
  }
  * { box-sizing: border-box; margin: 0; padding: 0; }
  html, body { width: 1200px; height: 576px; overflow: hidden; }
  body { background: var(--stage); position: relative; font-family: "Open Sans", sans-serif; }

  .card {
    position: absolute; top: 138px; width: 484px; height: 294px;
    border-radius: 14px; overflow: hidden; background: var(--card-white);
    box-shadow: 0 3px 6px rgba(0,0,0,.25);
  }
  .card--services { left: 82px; }
  .card--contact { left: 602px; top: 137px; }

  /* Name plate: plain name in the text face, one colour, one weight */
  .brand__name {
    font-family: "Open Sans", sans-serif; font-weight: 600;
    line-height: 1; letter-spacing: .3px;
  }

  /* Services side */
  .services__header { position: absolute; inset: 0; }
  .brand--light {
    position: absolute; top: 50px; left: 0; right: 0;
    display: flex; justify-content: center; align-items: center; gap: 12px;
    color: #fff;
  }
  .brand--light .brand__name { font-size: 24px; }
  .brand__square { width: 36px; height: 36px; background: #fff; }

  .services {
    position: absolute; top: 160px; left: 8px; right: 8px;
    display: flex; justify-content: space-between; list-style: none;
  }
  .service {
    flex: 1; display: flex; flex-direction: column; align-items: center;
    border-left: 1px solid rgba(142,10,12,.6);
    font-family: "Roboto", sans-serif; font-size: 11.5px; color: var(--ink);
    text-align: center; line-height: 1.3;
  }
  .service:first-child { border-left: none; }
  .service__icon { width: 34px; height: 40px; background: var(--brand-red); opacity: .85; margin-bottom: 9px; border-radius: 2px; }
  .services__web {
    position: absolute; top: 264px; left: 0; right: 0;
    display: flex; justify-content: center; align-items: center; gap: 10px;
    font-family: "Roboto", sans-serif; font-size: 11.5px; color: var(--ink);
  }
  .services__web::before, .services__web::after { content: ""; width: 94px; height: 1.5px; background: var(--brand-red); }
  .accent { color: var(--brand-red); }

  /* Contact side */
  .brand--dark { position: absolute; top: 40px; left: 30px; color: var(--charcoal); }
  .brand--dark .brand__name { font-size: 30px; }

  .region-band {
    position: absolute; top: 119px; left: 0; width: 322px; height: 83px;
    background: var(--brand-red); color: #fff; padding: 13px 0 0 32px;
    font-family: "Roboto", sans-serif;
  }
  .region-band__title { font-weight: 900; font-size: 17px; line-height: 1.25; letter-spacing: .2px; }
  .region-band__since {
    display: flex; align-items: center; gap: 6px; margin-top: 2px;
    font-size: 9px; letter-spacing: .6px; width: 160px;
  }
  .region-band__since::before, .region-band__since::after { content: ""; flex: 1; height: 1px; background: #fff; }
  .region-band--tail { left: 450px; width: 34px; padding: 0; }
  .mark-square { position: absolute; top: 100px; left: 333px; width: 108px; height: 108px; background: var(--charcoal); }

  .contact-list { position: absolute; top: 218px; left: 36px; list-style: none; font-size: 12.5px; color: var(--ink); }
  .contact-list li { display: flex; align-items: center; gap: 10px; height: 19.5px; }
  .contact-list svg { width: 11px; height: 11px; fill: var(--brand-red); }
  .promise { position: absolute; top: 246px; right: 29px; text-align: right; font-size: 12px; color: var(--ink); line-height: 1.55; }
</style>
</head>
<body>

<section class="card card--services" aria-label="Services side">
  <svg class="services__header" viewBox="0 0 484 294" aria-hidden="true">
    <path d="M0 0H484V104C360 116 250 150 130 130C80 122 30 110 0 102Z" fill="var(--brand-red)"/>
    <path d="M484 104V118C360 126 250 156 130 136C80 128 30 116 0 104C60 120 100 128 130 130C250 150 360 116 484 104Z" fill="var(--sliver)"/>
  </svg>
  <div class="brand brand--light">
    <span class="brand__square"></span>
    <span class="brand__name">FLUE GUARDIAN</span>
  </div>
  <ul class="services">
    <li class="service"><span class="service__icon" role="img" aria-label="Brick chimney icon"></span>Full Masonry<br>Services</li>
    <li class="service"><span class="service__icon" role="img" aria-label="Brick wall with handshake icon"></span>Historic Chimney<br>Restoration</li>
    <li class="service"><span class="service__icon" role="img" aria-label="Steel liner in chimney icon"></span>Stainless<br>Steel Liners</li>
    <li class="service"><span class="service__icon" role="img" aria-label="Bricks and trowel icon"></span>New Chimney<br>Installations</li>
    <li class="service"><span class="service__icon" role="img" aria-label="Chimney sweep brush icon"></span>Guild Certified<br>Chimney sweeps</li>
  </ul>
  <p class="services__web"><span>www.<span class="accent">flueguardianvt</span>.example</span></p>
</section>

<section class="card card--contact" aria-label="Contact side">
  <div class="brand brand--dark">
    <span class="brand__name">FLUE GUARDIAN</span>
  </div>
  <div class="region-band">
    <p class="region-band__title">SERVING VT AND<br>NEW HAMPSHIRE</p>
    <p class="region-band__since">SINCE 1989</p>
  </div>
  <div class="region-band region-band--tail"></div>
  <span class="mark-square"></span>
  <ul class="contact-list">
    <li><svg viewBox="0 0 12 12" aria-hidden="true"><path d="M1 4C1 2 3 1 6 1S11 2 11 4H8.5V3H3.5V4ZM2 6L4 4H8L10 6V11H2Z"/></svg>802-555-0147</li>
    <li><svg viewBox="0 0 12 12" aria-hidden="true"><path d="M0 2H12V3L6 7L0 3ZM0 4.5L6 8.5L12 4.5V10H0Z"/></svg>info@flueguardianvt.example</li>
    <li><svg viewBox="0 0 12 12" aria-hidden="true"><circle cx="6" cy="6" r="4.5"/></svg><span>www.<span class="accent">flueguardianvt</span>.example</span></li>
  </ul>
  <p class="promise">Fully Insured – Free Estimates<br>Family Owned &amp; Operated</p>
</section>

</body>
</html>
```